Development of musical artist Tavro Quill's Website

I need a website designed for a reggae musical artist by the name of Tavro Quill. The site should be representative of a Reggae artist from Jamaica that has a Caribbean appeal but also attractive to global audiences. The website should be responsive for all devices (desktop, laptop, mobile). It should be optimized for SEO purposes. Icons for Photoshare, Friendbook, Chirper, VideoHub should be included. The sections of the website should be as follows: Home, Media, News, Bio, Join, Contact. The 'Join' section should be a form for database collection to the fan club. I would like to easily be able to dump this database in an excel or .csv file at any given time. The 'Media' section should be able to showcase video thumbnails and allow persons to play videos through the site and the videos will be fed from VideoHub. The 'News' section will be for announcements and or new releases where the artist is mentioned. The site should also be built in such a way that analytics can be easily implemented. This website should be the main call to action for this artist moving forward. I would also like the website to have a easy to use CMS platform (Wordpress perhaps). The URL for the website will be tavroquillstar.example. Here are the links for some of the social media pages:
VideoHub - https://www.videohub.example/user/TavroQuill
Photoshare - https://www.photoshare.example/tavroquill/
A good website to refer to from a design perspective is https://marvello.example/

Target Market(s)

Reggae and Pop music fans

Industry/Entity Type

Artists

Coding

Number of Pages Required

5+ page

Font styles to use
Sans Serif

Requirements
Must have
• Great design
Nice to have
• Parallax technology

```html
<!DOCTYPE html>
<html lang="en">
<head>
<meta charset="utf-8">
<title>Tavro Quill – Official Site</title>
<link rel="stylesheet" href="https://fonts.googleapis.com/css2?family=Saira:wght@400;500;600;700;800;900&family=Montserrat:wght@400;500;600;700&display=swap">
<style>
:root{
  --red:#ed1c24;
  --dark:#141414;
  --darker:#0d0d0d;
  --white:#ffffff;
  --ink:#111111;
  --grey:#777777;
  --line:#8a8a8a;
  --footer:#1b1b1b;
}
*{box-sizing:border-box;margin:0;padding:0}
html,body{width:1200px;height:3005px;overflow:hidden}
body{position:relative;background:var(--white);font-family:'Montserrat',sans-serif;color:var(--ink)}
.abs{position:absolute}

/* hero */
.hero-bg{left:0;top:0;width:1200px;height:640px;background:linear-gradient(90deg,#0b0b0b 0%,#1a1714 60%,#2a211b 100%);clip-path:polygon(0 0,1200px 0,1200px 480px,0 632px)}
.hero-photo{left:820px;top:120px;width:380px;height:420px;background:radial-gradient(ellipse at 55% 35%,#5a3a26 0%,#3a2619 45%,#1a1410 80%);clip-path:polygon(0 0,380px 0,380px 360px,0 460px)}
.logo{left:116px;top:44px;font-family:'Saira',sans-serif;font-weight:800;font-size:36px;color:var(--white);letter-spacing:1px;display:flex;align-items:center;gap:12px}
.logo-dot{width:14px;height:14px;border-radius:50%;background:var(--white)}
.nav{left:628px;top:46px;display:flex;gap:0;font-family:'Saira',sans-serif;font-size:18px;font-weight:500}
.nav a{color:var(--white);text-decoration:none;margin-right:28px}
.nav a.active{color:var(--red)}
.hero-frame{left:312px;top:206px;width:548px;height:222px;border:2px solid #555}
.hero-hello{left:312px;top:228px;width:574px;text-align:center;font-family:'Saira',sans-serif;font-size:32px;color:var(--white)}
.hero-name{left:312px;top:262px;width:574px;text-align:center;font-family:'Saira',sans-serif;font-weight:700;font-size:66px;color:var(--white);line-height:1.1}
.hero-sub{left:312px;top:348px;width:574px;text-align:center;font-size:15px;font-weight:500;line-height:24px;color:var(--white)}
.dots{display:flex;gap:12px;align-items:center}
.dot{width:10px;height:10px;border-radius:50%;background:#cfcfcf}
.dot.on{width:20px;height:20px;border:3px solid #cfcfcf;background:transparent;position:relative}
.dot.on::after{content:"";position:absolute;left:3px;top:3px;width:8px;height:8px;border-radius:50%;background:#cfcfcf}
.dot.red-on{border-color:var(--red)}
.dot.red-on::after{background:var(--red)}

/* join form */
.join{left:816px;top:394px;width:268px;height:302px;background:var(--red);padding:20px 30px 0 30px;color:var(--white);box-shadow:0 6px 14px rgba(0,0,0,.25)}
.join h2{font-family:'Saira',sans-serif;font-weight:600;font-size:26px;line-height:30px;margin-left:-2px}
.join p{font-size:13px;font-weight:700;line-height:17px;margin-top:4px;width:220px}
.field{display:block;width:202px;height:36px;background:var(--white);margin-top:7px;font-size:11px;font-style:italic;color:#666;padding:11px 18px}
.field:first-of-type{margin-top:14px}
.submit{display:block;width:102px;height:32px;border:2px solid var(--white);margin-top:16px;font-family:'Montserrat',sans-serif;font-weight:700;font-size:14px;color:var(--white);text-align:center;line-height:28px}

/* bio */
.bio-frame{left:112px;top:714px;width:348px;height:396px;border:5px solid var(--red)}
.bio-photo{left:146px;top:748px;width:350px;height:400px;background:linear-gradient(160deg,#f2f2f2 0%,#d9d9d9 45%,#b8b4ae 100%)}
.h-section{font-family:'Saira',sans-serif;font-weight:800;font-size:50px;line-height:1}
.bio-title{left:574px;top:752px;color:var(--ink)}
.bio-text{left:578px;top:830px;width:510px;font-size:15px;line-height:29px;color:var(--grey);text-align:justify;letter-spacing:.2px}
.btn-red{left:578px;top:1056px;width:162px;height:46px;background:var(--red);color:var(--white);font-weight:700;font-size:16px;text-align:center;line-height:46px}

/* media */
.media-bg{left:0;top:1200px;width:1200px;height:745px;background:var(--red);clip-path:polygon(0 90px,1200px 0,1200px 745px,0 620px)}
.media-title{left:0;top:1344px;width:1200px;text-align:center;color:var(--white)}
.video{top:1456px;width:458px;height:262px;border-radius:14px;overflow:hidden}
.video .thumb{position:absolute;inset:0}
.video .play{position:absolute;left:196px;top:78px;width:66px;height:66px;border:3px solid var(--white);border-radius:50%}
.video .play::after{content:"";position:absolute;left:24px;top:17px;border-left:22px solid var(--white);border-top:14px solid transparent;border-bottom:14px solid transparent;opacity:0}
.video .play svg{position:absolute;left:20px;top:16px}
.video .label{position:absolute;left:0;top:154px;width:100%;text-align:center;font-family:'Saira',sans-serif;font-weight:800;font-size:28px;color:var(--white)}
.v-left{left:-126px}
.v-center{left:370px}
.v-right{left:866px}
.t1{background:linear-gradient(135deg,#7fa7b6 0%,#5d7f8a 40%,#3a5f78 100%)}
.t2{background:linear-gradient(135deg,#2a2f6a 0%,#3b3f8f 45%,#14162e 100%)}
.t3{background:linear-gradient(135deg,#d4c9a0 0%,#6f8fa0 50%,#34476a 100%)}

/* news */
.news-title{left:0;top:1986px;width:1200px;text-align:center;color:var(--ink)}
.card{top:2076px;width:300px;height:384px;background:var(--white);box-shadow:0 2px 10px rgba(0,0,0,.14)}
.card .img{height:180px}
.card h3{font-family:'Saira',sans-serif;font-weight:700;font-size:20px;line-height:27px;margin:14px 26px 0 26px;color:var(--ink)}
.card p{font-size:15px;line-height:24px;color:#555;margin:8px 26px 0 26px}
.card .more{display:block;font-size:11px;font-weight:700;color:var(--red);margin:18px 26px 0 26px}
.n1{left:122px}.n2{left:450px}.n3{left:772px}
.i1{background:linear-gradient(135deg,#e6c24a 0%,#6b4a3a 50%,#2a2222 100%)}
.i2{background:linear-gradient(135deg,#6b2418 0%,#3a1510 55%,#1c0f0c 100%)}
.i3{background:linear-gradient(135deg,#9a3a3a 0%,#c8b6a8 50%,#4a3b3a 100%)}

/* footer */
.footer-bg{left:0;top:2556px;width:1200px;height:449px;background:var(--footer);clip-path:polygon(0 0,1200px 116px,1200px 449px,0 449px)}
.f-head{top:2704px;font-family:'Saira',sans-serif;font-weight:500;font-size:22px;color:var(--white)}
.f-links{left:112px;top:2756px;list-style:none}
.f-links li{font-size:13px;font-weight:600;color:var(--white);height:28.5px;display:flex;align-items:center;gap:10px}
.chev{width:7px;height:7px;border-right:1.5px solid #ccc;border-top:1.5px solid #ccc;transform:rotate(45deg)}
.posts{left:326px;top:2758px}
.post{display:flex;gap:12px;margin-bottom:22px}
.post .chev{margin-top:6px}
.post b{display:block;font-size:13px;font-weight:600;color:var(--white)}
.post span{display:block;font-size:12px;color:var(--red);margin-top:3px}
.contact{left:608px;top:2758px;font-size:12px;color:var(--white)}
.contact .row{display:flex;margin-bottom:14px;line-height:18px}
.contact dt{width:62px;font-weight:700}
.contact dd{font-size:12px;color:#ddd}
.social{left:914px;top:2760px;display:flex;gap:11px}
.social span{width:25px;height:25px;border:1.5px solid var(--white);border-radius:50%}
.copy{left:0;top:2962px;width:1200px;text-align:center;font-size:12px;font-weight:500;color:var(--white)}
</style>
</head>
<body>

<header>
  <div class="abs hero-bg"></div>
  <div class="abs hero-photo" role="img" aria-label="Portrait photo of Tavro Quill in a dark shirt"></div>
  <div class="abs logo"><span class="logo-dot"></span>TAVRO QUILL</div>
  <nav class="abs nav">
    <a class="active" href="#home">Home</a><a href="#media">Media</a><a href="#news">News</a><a href="#bio">Bio</a><a href="#join">Join</a><a href="#contact">Contact</a>
  </nav>
  <div class="abs hero-frame"></div>
  <div class="abs hero-hello">Hello! I am a Singer</div>
  <h1 class="abs hero-name">Tavro Quill</h1>
  <p class="abs hero-sub">Music only makes me stronger. Music speaks to the<br>heart in ways words cannot express.</p>
  <div class="abs dots" style="left:570px;top:486px"><span class="dot on"></span><span class="dot"></span><span class="dot"></span></div>
  <form class="abs join" id="join">
    <h2>Join</h2>
    <p>Lorem ipsum dolor sit amet, consectetur adipiscing</p>
    <span class="field">Your Name</span>
    <span class="field">Email</span>
    <span class="field">Your Phone Number</span>
    <span class="submit">Submit</span>
  </form>
</header>

<section id="bio">
  <div class="abs bio-frame"></div>
  <div class="abs bio-photo" role="img" aria-label="Photo of Tavro Quill in a white striped jacket"></div>
  <h2 class="abs h-section bio-title">Our Bio</h2>
  <p class="abs bio-text">Sed ut perspiciatis unde omnis iste natus error sit voluptatem accusantium doloremque laudantium, totam rem aperiam, eaque ipsa quae ab illo inventore veritatis et quasi architecto beatae vitae dicta sunt explicabo. Nemo enim ipsam voluptatem quia voluptas sit aspernatur aut odit aut fugit, sed quia consequuntur magni dolores eos qui ratione voluptatem sequi nesciunt. Neque porro quisquam est, qui dolorem ipsum quia dolor sit amet, consectetur, adipisci velit</p>
  <div class="abs btn-red">Read More</div>
</section>

<section id="media">
  <div class="abs media-bg"></div>
  <h2 class="abs h-section media-title">Media</h2>
  <div class="abs video v-left"><div class="thumb t1" role="img" aria-label="Music video still: artist seated outdoors"></div><div class="play"><svg width="30" height="34" viewBox="0 0 30 34"><path d="M4 3 L26 17 L4 31 Z" fill="none" stroke="#fff" stroke-width="3" stroke-linejoin="round"/></svg></div><div class="label">Music For Life</div></div>
  <div class="abs video v-center"><div class="thumb t2" role="img" aria-label="Music video still: artist in sunglasses"></div><div class="play"><svg width="30" height="34" viewBox="0 0 30 34"><path d="M4 3 L26 17 L4 31 Z" fill="none" stroke="#fff" stroke-width="3" stroke-linejoin="round"/></svg></div><div class="label">Music For Life</div></div>
  <div class="abs video v-right"><div class="thumb t3" role="img" aria-label="Music video still: artist with friends at a food stall"></div><div class="play"><svg width="30" height="34" viewBox="0 0 30 34"><path d="M4 3 L26 17 L4 31 Z" fill="none" stroke="#fff" stroke-width="3" stroke-linejoin="round"/></svg></div><div class="label">Music For Life</div></div>
  <div class="abs dots" style="left:564px;top:1774px"><span class="dot" style="background:#fff"></span><span class="dot on" style="border-color:#111"></span><span class="dot" style="background:#fff"></span></div>
</section>

<section id="news">
  <h2 class="abs h-section news-title">News</h2>
  <article class="abs card n1"><div class="img i1" role="img" aria-label="News photo: artist with a friend"></div><h3>Sed ut perspiciatis unde omnis iste natus</h3><p>At vero eos et accusamus et iusto odio dignissimos ducimus qui blanditiis praesentium voluptatum</p><span class="more">READ MORE</span></article>
  <article class="abs card n2"><div class="img i2" role="img" aria-label="News photo: artist in a studio"></div><h3>Sed ut perspiciatis unde omnis iste natus</h3><p>At vero eos et accusamus et iusto odio dignissimos ducimus qui blanditiis praesentium voluptatum</p><span class="more">READ MORE</span></article>
  <article class="abs card n3"><div class="img i3" role="img" aria-label="News photo: artist at a holiday gathering"></div><h3>Sed ut perspiciatis unde omnis iste natus</h3><p>At vero eos et accusamus et iusto odio dignissimos ducimus qui blanditiis praesentium voluptatum</p><span class="more">READ MORE</span></article>
  <div class="abs dots" style="left:564px;top:2507px"><span class="dot" style="background:#999"></span><span class="dot on red-on"></span><span class="dot" style="background:#999"></span></div>
</section>

<footer id="contact">
  <div class="abs footer-bg"></div>
  <h4 class="abs f-head" style="left:112px">Quick Links</h4>
  <h4 class="abs f-head" style="left:324px">Recent Post</h4>
  <h4 class="abs f-head" style="left:602px">Contact Us</h4>
  <h4 class="abs f-head" style="left:910px">Stay Connected</h4>
  <ul class="abs f-links">
    <li><span class="chev"></span>Home</li><li><span class="chev"></span>Media</li><li><span class="chev"></span>News</li><li><span class="chev"></span>Bio</li><li><span class="chev"></span>Join</li><li><span class="chev"></span>Contact</li>
  </ul>
  <div class="abs posts">
    <div class="post"><span class="chev"></span><div><b>Lorem ipsum dolor sit amet</b><span>Jan 11, 2019</span></div></div>
    <div class="post"><span class="chev"></span><div><b>Lorem ipsum dolor sit amet</b><span>Jan 11, 2019</span></div></div>
  </div>
  <dl class="abs contact">
    <div class="row"><dt>Address:</dt><dd>4470 Harbour Lane,<br>Suite # 12, Port Vale, KT 30418</dd></div>
    <div class="row"><dt>Phone:</dt><dd>(555) 014 2290</dd></div>
    <div class="row"><dt>Fax:</dt><dd>1-555-014-2291</dd></div>
    <div class="row"><dt>Email:</dt><dd>info@tavroquill.example</dd></div>
  </dl>
  <div class="abs social">
    <span role="img" aria-label="Friendbook"></span><span role="img" aria-label="Chirper"></span><span role="img" aria-label="VideoHub"></span><span role="img" aria-label="Photoshare"></span>
  </div>
  <p class="abs copy">© 2019 Copyrights | All Rights Reserved</p>
</footer>

</body>
</html>
```